E-Book-Cover für meinen Roman Wo der Nebel wandert
Sehr angenehmer Kontakt, das Beschriebene wurde auf Anhieb in die Richtung umgesetzt, die ich angestrebt habe. Änderungswünsche wurden prompt und unermüdlich umgesetzt, bis das Endergebnis stand. Sehr zu empfehlen!
Zielgruppe
Ich veröffentliche in Eigenregie meinen Roman namens 'Wo der Nebel wandert' im Rahmen des Self-Publishing Angebots von Buchvolk.de
Bei meinem Werk handelt es sich um Belletristik: eine Geschichte aus dem Leben, die traurige und lustige Elemente zu gleichen Teilen eint. Behandelt wird der Lebensabschnitt eines Jugendlichen, der zu früh Erfahrung mit dem Tod macht, als seine Mutter schwer erkrankt. Gleichzeitig gilt es, den (humorvoll verpackten) Alltag zu meistern, in dem er wieder und wieder auf Ablehnung und Distanz angesichts seiner ungewöhnlichen und misslichen Lage stößt. Es gelingt ihm nicht mehr, Teil seiner gleichaltrigen Mitstreiter zu werden.
Gleichzeitig gibt es einen zweiten Handlungsstrang, in dem eine ebenfalls Jugendliche ähnliche Erfahrungen macht, auch wenn die Umstände andere sind, ebenso wie die Reaktion darauf. Während der männliche Protagonist wiederholt von seinem Umkreis enttäuscht wird, stellt er sich am Ende der Prüfung, der er nicht entkommen kann. Sein weibliches Pendant hingegen tritt eine überstürzte Flucht mit ungewissem Ausgang an. Beide Stränge sind lose miteinander verwoben, und als Leser stellt man sich zusehends die Frage, ob und wann diese verbunden werden. Eine Auflösung erfolgt am Schluss.
Nach einigen Testlesern stellte sich heraus, dass jene am meisten begeistert waren, die selbst ähnliche Erfahrungen gemacht haben, wie die fiktiven Personen. Grundsätzlich lässt sich aber sagen, dass der Schreibstil, die beschriebenen Medien und Situationen eher auf (junge) Erwachsene zugeschnitten sind. Dennoch handelt es sich nicht um ein klassisches Jugendbuch, oft werden Dinge beschrieben, die für Minderjährige nicht geeignet sind. Als (Haupt)zielgruppe würde ich grob den Rahmen 20-40 Jahre vorgeben, wobei die Leser eher noch älter als jünger sein dürfen.
Aufgabenstellung
Zunächst technisch: (Angaben lt. Buchvolk)
JPEG oder TIFF-Datei
mindestens 1000 Pixel an der längsten Seite
Idealverhältnis von Bildhöhe- und breite: 1,6 (Beispiel: 1000 x 1600)
bei weißen Covern sollte ein 2-3 Pixel breiter, grauer Rand hinzugefügt werden, damit sich das Cover von der Website selbst abhebt
Weiterhin zu beachten:
-Hauptsächlich wird es auf eBook Readern gelesen, die nur in Graustufen darstellen. Das Cover sollte also in jedem Fall auch in Schwarz-Weiß nichts von seiner Wirkung einbüßen!
Selbiges gilt für eine Miniaturansicht!
Autor: Matthias Kolwerth
Titel: Wo der Nebel wandert
Zusatz: Roman
Nun zu den wichtigsten Vorgaben:
-Selbstverständlich soll das Cover Aufmerksamkeit erzeugen und neugierig machen.
-Das Thema "anders sein" / "im Abseits stehen" / "hin- und hergetrieben werden" muss auf jeden Fall rübergebracht werden, da dies auch das Kernthema des Buches ist.
-Bei der Schriftart gibt es keine bestimmte Vorgabe, nur bitte nichts in Kapitälchen oder Großbuchstaben. (z.B. WO DER NEBEL WANDERT)
-Es soll auf keinen Fall übertrieben ernst oder möchtegern-schnulzig rüberkommen. (Bilder vom Strand, untergehender Sonne und weitere Klischees.)
-Vielmehr darf man dem Cover bereits ansehen, dass es ein ernstes Thema auch mit Humor nehmen kann. z.B. durch Stilisierung, einfache Farben anstatt aufwändiger Realaufnahmen und Schatten, evtl. auch in Richtung Comic, aber nicht zu albern.
-Die Platzierung von Autor und Titel darf klassisch sein, gerne aber auch ungewöhnlich überraschend.
Ich habe diesem Inserat einige Entwürfe meinerseits beigefügt, wie ich das o.g. Thema stilisieren würde, z.B.:
der Querschnitt eines einfahrenden Zuges (Hauptverkehrsmittel im Buch), bei dem in allen Fenstern Licht brennt, mit Ausnahme von einem. (Hier dürfen gerne auch die Profile von Menschen hinzug..

```html
<!DOCTYPE html>
<html lang="de">
<head>
<meta charset="utf-8">
<title>Wo der Nebel wandert – Matthias Kolwerth</title>
<link rel="stylesheet" href="https://fonts.googleapis.com/css2?family=Exo+2:wght@500;700;800&display=swap">
<style>
  :root {
    --page: #ffffff;
    --frame: #dadada;
    --indigo: #463f88;
    --magenta: #b05b95;
    --lilac: #bb8cbb;
    --lavender: #a6a4cc;
    --ink: #1a1a1a;
  }
  html, body {
    margin: 0;
    padding: 0;
    width: 882px;
    height: 1200px;
    overflow: hidden;
    background: var(--page);
  }
  .canvas {
    position: relative;
    width: 882px;
    height: 1200px;
    background: var(--page);
  }
  .cover {
    position: absolute;
    left: 159px;
    top: 140px;
    width: 531px;
    height: 868px;
    border: 11px solid var(--frame);
    background: var(--page);
    box-shadow: 1px 2px 2px rgba(0,0,0,0.12);
    overflow: hidden;
    font-family: "Exo 2", "Trebuchet MS", sans-serif;
  }
  .cover__scene {
    position: absolute;
    left: 0;
    top: 0;
    width: 531px;
    height: 530px;
    background: linear-gradient(
      to bottom,
      var(--page) 0%,
      var(--page) 17%,
      var(--magenta) 19%,
      var(--magenta) 46%,
      var(--lilac) 52%,
      var(--page) 56%,
      var(--lavender) 59%,
      var(--indigo) 63%,
      #d7d6e6 70%,
      var(--page) 100%
    );
  }
  .title {
    position: absolute;
    left: 0;
    width: 100%;
    margin: 0;
    text-align: center;
    font-weight: 800;
    line-height: 1;
    letter-spacing: -0.5px;
  }
  .title__line {
    position: absolute;
    left: 0;
    width: 100%;
    text-align: center;
    white-space: nowrap;
  }
  .title__line--first {
    top: 448px;
    font-size: 60px;
    color: var(--indigo);
  }
  .title__line--second {
    top: 504px;
    color: var(--indigo);
  }
  .title__small {
    font-size: 60px;
    color: var(--indigo);
  }
  .title__accent {
    font-size: 86px;
    color: var(--magenta);
    margin-left: 6px;
  }
  .title__line--third {
    top: 600px;
    font-size: 60px;
    color: var(--indigo);
  }
  .genre {
    position: absolute;
    top: 662px;
    left: 0;
    width: 100%;
    text-align: center;
    font-weight: 700;
    font-size: 22px;
    color: var(--magenta);
    margin: 0;
  }
  .author {
    position: absolute;
    top: 720px;
    left: 0;
    width: 100%;
    text-align: center;
    font-weight: 500;
    font-size: 29px;
    color: var(--ink);
    margin: 0;
  }
</style>
</head>
<body>
  <div class="canvas">
    <div class="cover">
      <div class="cover__scene" role="img" aria-label="Stilisierte Zeichnung: Bahngleise mit Oberleitungen laufen zum Horizont, darüber ein violetter Himmel"></div>
      <h1 class="title">
        <span class="title__line title__line--first">Wo</span>
        <span class="title__line title__line--second"><span class="title__small">der</span><span class="title__accent">Nebel</span></span>
        <span class="title__line title__line--third">wandert</span>
      </h1>
      <p class="genre">Roman</p>
      <p class="author">Matthias Kolwerth</p>
    </div>
  </div>
</body>
</html>
```